Homemaking training schools needs a Business Card design

Designer, Hello!

No special requirements, good-looking enough.
--------------------------------------------------------------------------

Name: Marcus Dole
Chairman
Tel: 0574-71948263
Mobile: 13857420916
Email: kelvora@mailnest.example
Web: www.prt2019.example
Add: No.258, LanpingJie, BeiyuanQu, Ningbo, Zhejiang

LOGO
Ningbo PRT Homemaking Training School

Target Market(s)

pregnant women, mothers, infants, the elderly and families, including cleaning, cooking, nursing training.

Industry/Entity Type

Business

Contact Information for Business Card

Name: Marcus Dole
Chairman
Tel: 0574-71948263
Mobile: 13857420916
Email: kelvora@mailnest.example
Web: www.prt2019.example

LOGO

Font styles to use
Serif
Sans Serif
Decorative

Requirements
Nice to have
• Feels: clean, specifications, safety, comfort, warmth and happiness.

```html
<!DOCTYPE html>
<html lang="en">
<head>
<meta charset="utf-8">
<title>PinRuiTang Business Card</title>
<link href="https://fonts.googleapis.com/css2?family=Montserrat:wght@500;600&family=Open+Sans:wght@400;600&display=swap" rel="stylesheet">
<style>
  :root {
    --backdrop: #585858;
    --card-light: #ffffff;
    --card-dark: #000000;
    --brand-blue: #1f73b7;
    --brand-pink: #e5198a;
    --ink: #2a2a2a;
    --text-light: #f2f2f2;
  }
  html, body {
    margin: 0;
    padding: 0;
    width: 1105px;
    height: 1200px;
    overflow: hidden;
    background: var(--backdrop);
  }
  .canvas {
    position: relative;
    width: 1105px;
    height: 1200px;
  }
  .card {
    position: absolute;
    left: 196px;
    width: 720px;
    height: 412px;
    box-sizing: border-box;
  }
  .card--front { top: 146px; background: var(--card-light); }
  .card--back { top: 602px; height: 410px; background: var(--card-dark); text-align: center; }

  .brand {
    position: absolute;
    left: 0;
    right: 0;
    top: 350px;
    top: 204px;
    text-align: center;
  }
  .brand__name {
    font-family: "Montserrat", sans-serif;
    font-weight: 600;
    font-size: 42px;
    line-height: 44px;
    color: var(--ink);
    letter-spacing: 0.5px;
  }
  .brand__tagline {
    display: flex;
    align-items: center;
    justify-content: center;
    gap: 10px;
    margin-top: 6px;
    font-family: "Open Sans", sans-serif;
    font-size: 16px;
    line-height: 22px;
    color: #333;
  }
  .brand__tagline::before,
  .brand__tagline::after {
    content: "";
    width: 70px;
    height: 2px;
    background: #222;
  }

  .back-mark {
    position: absolute;
    left: 0;
    right: 0;
    top: 90px;
    font-family: "Montserrat", sans-serif;
    font-weight: 600;
    font-size: 20px;
    line-height: 24px;
    color: var(--text-light);
  }
  .back-rule {
    position: absolute;
    left: 160px;
    top: 127px;
    width: 400px;
    height: 1px;
    background: linear-gradient(90deg, transparent, #5a1034 50%, transparent);
  }
  .person__name {
    position: absolute;
    left: 0; right: 0;
    top: 172px;
    margin: 0;
    font-family: "Montserrat", sans-serif;
    font-weight: 500;
    font-size: 28px;
    letter-spacing: 1px;
    color: var(--brand-blue);
  }
  .person__title {
    position: absolute;
    left: 0; right: 0;
    top: 210px;
    margin: 0;
    font-family: "Montserrat", sans-serif;
    font-weight: 500;
    font-size: 20px;
    letter-spacing: 1px;
    color: var(--brand-pink);
  }
  .contact {
    position: absolute;
    left: 0; right: 0;
    top: 258px;
    font-family: "Open Sans", sans-serif;
    font-size: 18px;
    line-height: 27px;
    color: var(--text-light);
  }
  .contact p { margin: 0; }
  .contact__label {
    font-weight: 600;
    color: var(--brand-pink);
  }
</style>
</head>
<body>
<div class="canvas">
  <section class="card card--front">
    <div class="brand">
      <div class="brand__name">PinRuiTang</div>
      <div class="brand__tagline">Training &amp; Services</div>
    </div>
  </section>

  <section class="card card--back">
    <div class="back-mark">PinRuiTang</div>
    <div class="back-rule"></div>
    <h1 class="person__name">MARCUS DOLE</h1>
    <h2 class="person__title">CHAIRMAN</h2>
    <div class="contact">
      <p>No.258, LanpingJie, BeiyuanQu, Ningbo, Zhejiang</p>
      <p><span class="contact__label">P :</span> 0574-71948263 <span class="contact__label">M :</span> 13857420916</p>
      <p><span class="contact__label">E :</span> kelvora@mailnest.example &nbsp;<span class="contact__label">W :</span> www.prt2019.example</p>
    </div>
  </section>
</div>
</body>
</html>
```